IT Freelancer (Consulting, trainer and project manager) needed letterhead

As a freelancer for IT Trainingswhip, consulting and project management I need a letterhead design. What is desired is a design that fits the existing logo (see Annex). It is functional, reliable, and equal time wirkenn Agil and modern. The whole is in color, as well as printed out to make a good impression on a black and white printer. The whole is to the existing Cooperate design (business card, homepage, logo) fit. Therefore, the choice of colors.
Updates

Target Market(s)

Customers such as medium-sized enterprises, training institutions

Industry/Entity Type

Consulting

Colors
0455a3
3277b5
85abd2
cfdfed
34a6d7
32a6d6
249fd4
0792cd
85cae6

Requirements
Must have
• Must include logo (see Annex) address (Brunnerweg 14, 95617 Tannfeld, Germany). Must seriously and act simultaneously Agil. Design should (even) be adaptable (signature, address, etc.) design must look good on a black / white laser

```html
<!DOCTYPE html>
<html lang="de">
<head>
<meta charset="utf-8">
<title>Lukas Brenner – Briefbogen</title>
<link href="https://fonts.googleapis.com/css2?family=Lato:wght@400;700;900&display=swap" rel="stylesheet">
<style>
  :root {
    --backdrop: #e9eaec;
    --paper: #ffffff;
    --brand-deep: #0455a3;
    --brand-sky: #249fd4;
    --brand-light: #85cae6;
    --brand-pale: #cfdfed;
    --ink: #3a3f47;
    --ink-soft: #6b7079;
    --watermark: #f3f4f6;
  }
  * { box-sizing: border-box; margin: 0; padding: 0; }
  html, body {
    width: 1200px; height: 794px; overflow: hidden;
    background: var(--backdrop);
    font-family: "Lato", sans-serif;
    color: var(--ink);
  }
  .letterhead {
    position: absolute; left: 330px; top: 15px;
    width: 540px; height: 764px;
    background: var(--paper);
    box-shadow: 0 6px 24px rgba(0,0,0,.12);
    overflow: hidden;
  }
  .side-band {
    position: absolute; left: 0; top: 0; bottom: 0; width: 20px;
    background: var(--brand-deep);
  }
  .band-accents { position: absolute; left: 0; top: 176px; width: 48px; height: 70px; }
  .web-address {
    position: absolute; left: 4px; bottom: 22px;
    writing-mode: vertical-rl; transform: rotate(180deg);
    color: #fff; font-size: 10px; letter-spacing: .3px; white-space: nowrap;
  }
  .circuit-art {
    position: absolute; left: 30px; top: 0; width: 150px; height: 160px;
    background: linear-gradient(180deg, #ffffff 0%, #d6edf8 30%, #a9d9ee 100%);
    border-radius: 0 0 8px 8px;
  }
  .sender-line {
    position: absolute; left: 52px; top: 176px;
    font-size: 6px; color: var(--ink-soft); letter-spacing: .1px; white-space: nowrap;
  }
  .contact-block {
    position: absolute; left: 300px; top: 38px;
    font-size: 7px; line-height: 9.5px; color: var(--ink); font-style: normal;
  }
  .contact-block .row { display: flex; align-items: center; gap: 4px; padding-left: 2px; }
  .contact-block svg { width: 6px; height: 6px; fill: var(--brand-deep); }
  .divider {
    position: absolute; left: 408px; top: 30px; width: 1px; height: 56px;
    background: var(--brand-light);
  }
  .brand {
    position: absolute; left: 420px; top: 26px;
    display: flex; flex-direction: column; align-items: center; gap: 5px;
  }
  .brand-dot { width: 34px; height: 34px; border-radius: 50%; background: var(--brand-deep); }
  .brand-name {
    font-weight: 900; font-size: 11px; line-height: 11px;
    color: var(--brand-deep); text-align: center; letter-spacing: .6px;
  }
  .watermark-disc {
    position: absolute; left: 250px; top: 330px;
    width: 260px; height: 260px; border-radius: 50%;
    background: var(--watermark);
  }
</style>
</head>
<body>
  <main class="letterhead">
    <div class="circuit-art" role="img" aria-label="Blue circuit-board line decoration"></div>
    <div class="side-band"></div>
    <svg class="band-accents" viewBox="0 0 48 70" aria-hidden="true">
      <polygon points="0,0 24,0 30,8 0,8" fill="#ffffff"/>
      <polygon points="0,12 30,12 38,28 0,28" fill="#34a6d7"/>
      <polygon points="0,32 38,32 44,46 0,46" fill="#85cae6"/>
      <polygon points="0,50 44,50 46,58 0,58" fill="#cfdfed"/>
    </svg>
    <div class="web-address">www.lukasbrenner.de</div>

    <p class="sender-line">Lukas Brenner · Brunnerweg 14 · 95617 Tannfeld · Deutschland</p>

    <address class="contact-block">
      <div>Brunnerweg 14</div>
      <div>95617 Tannfeld</div>
      <div>Deutschland</div>
      <div class="row"><svg viewBox="0 0 10 10"><path d="M2 1l2 0 1 2-1 1c1 2 2 3 3 3l1-1 2 1v2c-5 0-8-4-8-8z"/></svg>0931 47 28 15</div>
      <div class="row"><svg viewBox="0 0 10 10"><rect x="1" y="3" width="8" height="6" rx="1"/><rect x="3" y="0" width="4" height="3"/></svg>0931 47 28 19</div>
      <div class="row"><svg viewBox="0 0 10 10"><rect x="0" y="2" width="10" height="7" rx="1"/></svg>info@lukasbrenner.de</div>
    </address>

    <div class="divider"></div>
    <div class="brand">
      <div class="brand-dot"></div>
      <div class="brand-name">LUKAS<br>BRENNER</div>
    </div>

    <div class="watermark-disc" aria-hidden="true"></div>
  </main>
</body>
</html>
```